Dalvick's Business Card

I need some designs for a new business card including the new logo attached. An old example of our business card is also attached to show all the data that should be included on the new design.
**I added some more examples someone had mocked up**

Contact Information for Business Card

Should include all info on other examples uploaded.

```html
<!DOCTYPE html>
<html lang="en">
<head>
<meta charset="utf-8">
<title>Dalvick's Business Card</title>
<link href="https://fonts.googleapis.com/css2?family=Montserrat:wght@500;600;700;800&family=Lexend:wght@300;400&display=swap" rel="stylesheet">
<style>
  :root {
    --blue: #0b6bb3;
    --blue-light: #1583c6;
    --red: #d4191f;
    --white: #ffffff;
    --card: #f3f3f3;
    --backdrop: #e3e3e3;
  }
  html, body { margin: 0; padding: 0; overflow: hidden; }
  body {
    width: 1200px; height: 1200px;
    background: var(--backdrop);
    position: relative;
    font-family: "Montserrat", sans-serif;
  }
  .card {
    position: absolute;
    left: 227px;
    width: 705px; height: 402px;
    background: linear-gradient(135deg, #ededed 0%, #f6f6f6 60%, #efefef 100%);
    overflow: hidden;
  }
  .card--front { top: 155px; }
  .card--back { top: 610px; }
  .card svg.shapes { position: absolute; inset: 0; }
  .band-text {
    position: absolute; left: 212px;
    color: var(--white);
    font-size: 15px; font-weight: 500; letter-spacing: 0.3px;
    line-height: 23px; text-transform: uppercase;
  }
  .band-text b { font-weight: 700; }
  .band-text--top { top: 30px; }
  .band-text--bottom { top: 328px; }
  .brand-dot {
    position: absolute; left: 112px; top: 160px;
    width: 96px; height: 96px; border-radius: 50%;
    background: var(--blue);
  }
  .brand-name {
    position: absolute; left: 225px; top: 160px;
    font-size: 62px; font-weight: 600; color: var(--blue);
    line-height: 1; letter-spacing: -0.5px;
  }
  .brand-tagline {
    position: absolute; left: 228px; top: 226px;
    font-size: 15.6px; font-weight: 600; color: var(--red);
    letter-spacing: 0.2px;
  }
  .person-name {
    position: absolute; left: 78px; top: 83px;
    font-size: 30px; font-weight: 800; color: var(--red);
    letter-spacing: 0.3px;
  }
  .contact {
    position: absolute; left: 77px;
    font-family: "Lexend", sans-serif; font-weight: 300;
    font-size: 21px; color: var(--blue);
    display: flex; align-items: center; gap: 7px;
  }
  .contact svg { width: 17px; height: 17px; }
  .contact--phone { top: 208px; }
  .contact--email { top: 240px; }
  .back-mark-dot {
    position: absolute; left: 506px; top: 92px;
    width: 84px; height: 84px; border-radius: 50%;
    background: var(--blue);
  }
  .back-mark-name {
    position: absolute; left: 468px; top: 190px; width: 160px;
    text-align: center;
    font-size: 30px; font-weight: 600; color: var(--blue);
  }
  .pill-text {
    position: absolute; top: 355px;
    font-family: "Lexend", sans-serif; font-weight: 300;
    font-size: 21px; color: var(--white);
    text-align: center; letter-spacing: 0.5px;
  }
  .pill-text--family { left: 30px; width: 340px; }
  .pill-text--licensed { left: 400px; width: 280px; }
</style>
</head>
<body>

  <section class="card card--front">
    <svg class="shapes" viewBox="0 0 705 402" width="705" height="402" aria-hidden="true">
      <defs>
        <linearGradient id="bandGrad" x1="0" y1="0" x2="1" y2="0">
          <stop offset="0" stop-color="#0b67ae"/>
          <stop offset="1" stop-color="#1583c6"/>
        </linearGradient>
      </defs>
      <polygon points="119,0 705,0 705,87 205,87" fill="url(#bandGrad)"/>
      <polygon points="205,316 705,316 705,402 119,402" fill="url(#bandGrad)"/>
    </svg>
    <div class="band-text band-text--top">Serves Maple Ridge, IA &amp; <b>Surrounding Areas</b></div>
    <div class="brand-dot"></div>
    <div class="brand-name">DALVICK'S</div>
    <div class="brand-tagline">AIR CONDITIONING &amp; HEATING SERVICE</div>
    <div class="band-text band-text--bottom">Call today for all your <b>HVAC,</b><br><b>Refrigeration</b> &amp; <b>Plumbing Needs</b></div>
  </section>

  <section class="card card--back">
    <svg class="shapes" viewBox="0 0 705 402" width="705" height="402" aria-hidden="true">
      <path d="M0,355 Q200,322 360,326 Q400,330 386,356 Q370,382 340,403 L0,403 Z" fill="var(--red)"/>
      <path d="M358,403 Q420,332 560,323 Q640,320 705,346 L705,403 Z" fill="var(--blue)"/>
    </svg>
    <div class="person-name">MARK DALVICK</div>
    <div class="contact contact--phone">
      <svg viewBox="0 0 24 24" aria-hidden="true"><path fill="var(--red)" d="M6.6 10.8a15.1 15.1 0 0 0 6.6 6.6l2.2-2.2c.3-.3.7-.4 1-.2 1.1.4 2.3.6 3.6.6.6 0 1 .4 1 1V20c0 .6-.4 1-1 1A17 17 0 0 1 3 4c0-.6.4-1 1-1h3.5c.6 0 1 .4 1 1 0 1.3.2 2.5.6 3.6.1.3 0 .7-.2 1z"/></svg>
      555.014.2287
    </div>
    <div class="contact contact--email">
      <svg viewBox="0 0 24 24" aria-hidden="true"><path fill="var(--red)" d="M2 5h20v14H2z"/><path fill="none" stroke="#f3f3f3" stroke-width="1.6" d="M2.5 6l9.5 7 9.5-7"/></svg>
      hvacdalvick@mail.com
    </div>
    <div class="back-mark-dot"></div>
    <div class="back-mark-name">Dalvick's</div>
    <div class="pill-text pill-text--family">Family Owned &amp; Operated</div>
    <div class="pill-text pill-text--licensed">Licensed &amp; insured</div>
  </section>

</body>
</html>
```